Envelope Design - Winner can do follow-up business

- Varnoko.com is a Swiss-based online store selling business shirts and accessories for business men
- Please visit the webpage to make yourself familiar with the company. Although the text is in German, with Plimbo translator you should be able to understand the main content.
- Our clients are mainly business men between 30 and 60 years old. Mostly with a high income working in the service industry (banking, insurance, lawyers, etc.). Sometimes there wives purchase the shirts for them ;-)
- The colors and the logo are given, as they are also used for the print materials (please see files in attachment)
- I am running several businesses and often need a talented web designer --> the winner gets substantial follow-up business
your task:
-for our company we need a new envelope design
-It should be simple and modern
-please use one of the logos in the followings.
-suprise me :)

```html
<!DOCTYPE html>
<html lang="en">
<head>
<meta charset="utf-8">
<title>Varnoko Envelope Design</title>
<link rel="stylesheet" href="https://fonts.googleapis.com/css2?family=Montserrat:wght@500&family=Open+Sans:wght@400&display=swap">
<style>
  :root {
    --backdrop: #4a2e1c;
    --paper: #ffffff;
    --edge: #b9b9b9;
    --brand-yellow: #e7d86b;
    --brand-red: #ef2e24;
    --ink: #1e1e1e;
  }
  * { margin: 0; padding: 0; box-sizing: border-box; }
  html, body { width: 1200px; height: 962px; overflow: hidden; }
  body { background: var(--backdrop); position: relative; }

  .envelope {
    position: absolute;
    background: var(--paper);
    border: 1px solid var(--edge);
  }
  .envelope-back-yellow { left: 148px; top: 64px; width: 974px; height: 520px; }
  .envelope-back-red { left: 57px; top: 235px; width: 974px; height: 458px; }
  .envelope-front { left: 158px; top: 420px; width: 975px; height: 459px; }

  .flap { position: absolute; left: 0; top: 0; width: 100%; height: 160px; display: block; }
  .flap-yellow path { fill: var(--brand-yellow); }
  .flap-red path { fill: var(--brand-red); }

  .flap-wordmark {
    position: absolute;
    left: 0; right: 0; top: 44px;
    text-align: center;
    font-family: "Montserrat", sans-serif;
    font-weight: 500;
    font-size: 42px;
    letter-spacing: 3px;
    color: var(--brand-red);
    line-height: 1;
  }

  .front-band {
    position: absolute; left: 0; top: 0; width: 100%; height: 11px;
    background: var(--brand-yellow);
  }
  .front-wordmark {
    position: absolute;
    left: 28px; top: 106px;
    font-family: "Montserrat", sans-serif;
    font-weight: 500;
    font-size: 42px;
    letter-spacing: 3px;
    color: var(--brand-yellow);
    line-height: 1;
  }
  .contact-list {
    position: absolute; left: 28px; top: 376px;
    list-style: none;
    font-family: "Open Sans", sans-serif;
    font-size: 19px;
    color: var(--ink);
  }
  .contact-item { display: flex; align-items: center; height: 42px; }
  .contact-icon { width: 22px; height: 22px; margin-right: 12px; flex: none; }
  .contact-icon path, .contact-icon circle, .contact-icon line { stroke: var(--brand-red); fill: none; stroke-width: 1.6; }
  .contact-icon .pin-body { fill: var(--brand-red); stroke: none; }
  .contact-icon .pin-hole { fill: var(--paper); stroke: none; }
</style>
</head>
<body>
  <div class="envelope envelope-back-yellow">
    <svg class="flap flap-yellow" viewBox="0 0 974 160" preserveAspectRatio="none" aria-hidden="true">
      <path d="M0,0 H974 C962,42 952,68 880,80 L530,148 Q487,156 444,148 L94,80 C22,68 12,42 0,0 Z"/>
    </svg>
    <div class="flap-wordmark">VARNOKO</div>
  </div>

  <div class="envelope envelope-back-red">
    <svg class="flap flap-red" viewBox="0 0 974 160" preserveAspectRatio="none" aria-hidden="true">
      <path d="M0,0 H974 C962,42 952,68 880,80 L530,148 Q487,156 444,148 L94,80 C22,68 12,42 0,0 Z"/>
    </svg>
  </div>

  <div class="envelope envelope-front">
    <div class="front-band"></div>
    <div class="front-wordmark">VARNOKO</div>
    <ul class="contact-list">
      <li class="contact-item">
        <svg class="contact-icon" viewBox="0 0 22 22" aria-hidden="true">
          <circle cx="11" cy="11" r="9.5"/>
          <path d="M11,1.5 C6,6 6,16 11,20.5 M11,1.5 C16,6 16,16 11,20.5"/>
          <line x1="1.5" y1="11" x2="20.5" y2="11"/>
          <line x1="3" y1="6.5" x2="19" y2="6.5"/>
          <line x1="3" y1="15.5" x2="19" y2="15.5"/>
        </svg>
        <span>www.varnoko.com</span>
      </li>
      <li class="contact-item">
        <svg class="contact-icon" viewBox="0 0 22 22" aria-hidden="true">
          <path class="pin-body" d="M11,1 C6.5,1 3.5,4.3 3.5,8.5 C3.5,14 11,21.5 11,21.5 C11,21.5 18.5,14 18.5,8.5 C18.5,4.3 15.5,1 11,1 Z"/>
          <circle class="pin-hole" cx="11" cy="8.5" r="3"/>
        </svg>
        <span>Street Name, City Name, State Zipcode</span>
      </li>
    </ul>
  </div>
</body>
</html>
```